Stonebrace Business Card Design

The Stonebrace Co is an aggregate (crushing) equipment dealer serving Western Canadian provinces. Stonebrace is a distributor of aggregate equipment for different manufacturers.

We are looking to change and update the existing business card which has been used since the existence of the company. A copy of existing card has been attached for reference. The Stonebrace Co logo we want to remain the same and we want the green color to remain the same.

We are wanting something new with a different look. A refreshing card to show a new modern and updated look. No longer wanting to have the manufacturers on the back of the card but something more like our logo on the back of the card with a statement like "Crushing Solutions"

ideas could be:
- card can be different colors on front and back
- front or reverse of the card could possibly be the green color with the logo in black

Target Market(s)

Owners of Aggregate/Crushing companies

Contact Information for Business Card

see above

Requirements
Must have
• - logo to remain same along with same font within logo
• - green color to remain same
Nice to have
• as noted above under project description
Should not have

```html
<!DOCTYPE html>
<html lang="en">
<head>
<meta charset="utf-8">
<title>The Stonebrace Co – Business Card</title>
<link rel="stylesheet" href="https://fonts.googleapis.com/css2?family=Roboto:wght@400;500;700&family=Roboto+Condensed:wght@500;700&display=swap">
<style>
  :root {
    --brand-green: #878a0a;
    --ink: #1f1e1a;
    --text-grey: #4a4a48;
    --paper: #f7f7f5;
    --backdrop: #e9e8e4;
  }
  * { margin: 0; padding: 0; box-sizing: border-box; }
  html, body { width: 1200px; height: 960px; overflow: hidden; }
  body {
    background: var(--backdrop);
    font-family: "Roboto", Arial, sans-serif;
    position: relative;
  }
  .card {
    position: absolute;
    left: 320px;
    width: 600px;
    height: 344px;
    border-radius: 18px;
  }
  /* Front */
  .card-front {
    top: 104px;
    background: var(--brand-green);
  }
  .brand {
    position: absolute;
    left: 0; right: 0;
    top: 146px;
    display: flex;
    align-items: center;
    justify-content: center;
    gap: 22px;
  }
  .brand-dot {
    width: 46px; height: 46px;
    border-radius: 50%;
    background: var(--ink);
  }
  .brand-name {
    font-family: "Roboto Condensed", "Arial Narrow", sans-serif;
    font-weight: 700;
    font-size: 23px;
    color: var(--ink);
    letter-spacing: 0.2px;
  }
  .front-tagline {
    position: absolute;
    left: 0; right: 0;
    top: 294px;
    text-align: center;
    font-weight: 500;
    font-size: 15px;
    color: var(--ink);
  }
  /* Back */
  .card-back {
    top: 493px;
    background: var(--paper);
    overflow: hidden;
  }
  .person {
    position: absolute;
    right: 34px;
    top: 34px;
    text-align: right;
  }
  .person-name {
    font-family: "Roboto Condensed", "Arial Narrow", sans-serif;
    font-weight: 700;
    font-size: 21px;
    color: var(--brand-green);
    line-height: 1.05;
  }
  .person-role {
    font-size: 14px;
    font-weight: 500;
    color: var(--ink);
    margin-top: 4px;
    letter-spacing: 0.3px;
  }
  .contact-list {
    position: absolute;
    left: 32px;
    top: 198px;
    list-style: none;
    font-size: 14px;
    color: var(--text-grey);
  }
  .contact-list li {
    display: flex;
    align-items: center;
    gap: 7px;
    height: 19px;
  }
  .contact-list svg { width: 14px; height: 14px; fill: var(--brand-green); }
  .address {
    position: absolute;
    right: 34px;
    top: 212px;
    text-align: right;
    font-size: 14px;
    line-height: 19.5px;
    color: var(--text-grey);
  }
  .address .tagline {
    font-weight: 500;
    color: var(--ink);
    font-size: 14.5px;
  }
  .web-rule {
    position: absolute;
    left: 0; right: 0;
    top: 303px;
    height: 2px;
    background: var(--brand-green);
  }
  .web-pill {
    position: absolute;
    left: 33px;
    top: 289px;
    width: 240px;
    height: 28px;
    border-radius: 14px;
    background: var(--brand-green);
    color: #fff;
    font-size: 14px;
    letter-spacing: 2.6px;
    display: flex;
    align-items: center;
    justify-content: center;
  }
</style>
</head>
<body>

<section class="card card-front" aria-label="Card front">
  <div class="brand">
    <span class="brand-dot"></span>
    <span class="brand-name">THE STONEBRACE CO.</span>
  </div>
  <p class="front-tagline">Crushing Solutions</p>
</section>

<section class="card card-back" aria-label="Card back">
  <div class="person">
    <p class="person-name">DALE MORROW</p>
    <p class="person-role">CEO/FOUNDER</p>
  </div>

  <ul class="contact-list">
    <li>
      <svg viewBox="0 0 16 16" aria-hidden="true"><path d="M3.6 1.2l2.3 2.6-1.3 1.8c.9 2 2.4 3.6 4.4 4.6l1.8-1.3 2.6 2.3-1.4 2.4C6.6 13.4 2.6 9.4 1.2 3.8z"/></svg>
      <span>780.555.0142</span>
    </li>
    <li>
      <svg viewBox="0 0 16 16" aria-hidden="true"><path d="M4.5 0.5h7a1 1 0 0 1 1 1v13a1 1 0 0 1-1 1h-7a1 1 0 0 1-1-1v-13a1 1 0 0 1 1-1zm.5 2v10h6v-10zm3 10.8a.8.8 0 1 0 0 1.6.8.8 0 0 0 0-1.6z"/></svg>
      <span>780.555.0187</span>
    </li>
    <li>
      <svg viewBox="0 0 16 16" aria-hidden="true"><path d="M4 1h8v4H4zM1.5 6h13a1 1 0 0 1 1 1v5h-3v3h-9v-3h-3V7a1 1 0 0 1 1-1zm3 6v2h7v-2z"/></svg>
      <span>780.555.0163</span>
    </li>
    <li>
      <svg viewBox="0 0 16 16" aria-hidden="true"><path d="M1 3.5h14v1L8 9 1 4.5zM1 6l7 4.5L15 6v6.5H1z"/></svg>
      <span>dale@stonebr.com</span>
    </li>
  </ul>

  <div class="address">
    <p>2318- 48B Avenue</p>
    <p>Westfield, Alberta T4X 2M8</p>
    <p class="tagline">Crushing Solutions</p>
  </div>

  <div class="web-rule"></div>
  <div class="web-pill">www.stonebrace.ca</div>
</section>

</body>
</html>
```